Tolbek cards

I want a simple business card that pops.
Logo on one side.
On side two i want.
"Are you thinking about a new building on your property, or renovating an existing structure? Contact".....
Owners Name: Dale Whitacre
Owners Phone number: 610-555-0187
Address:4076 Copper Ridge RD, Millbrook, PA 16790
Committed to Quality, Service, and Integrity

```html
<!DOCTYPE html>
<html lang="en">
<head>
<meta charset="utf-8">
<title>Tolbek Builders LLC – Business Cards</title>
<link rel="stylesheet" href="https://fonts.googleapis.com/css2?family=Arimo:wght@400;700&display=swap">
<style>
  :root {
    --stage: #2a2a2a;
    --card: #f1f0ee;
    --brown-dark: #4b3322;
    --brown-mid: #6e4f39;
    --tan: #a68a6d;
    --tan-light: #c2a98d;
    --ink: #3b2a1e;
    --ink-soft: #4a3a2e;
    --white: #ffffff;
  }
  * { box-sizing: border-box; margin: 0; padding: 0; }
  html, body { width: 1200px; height: 576px; overflow: hidden; }
  body {
    background: var(--stage);
    font-family: "Arimo", Arial, sans-serif;
    position: relative;
  }
  .card {
    position: absolute;
    top: 139px;
    width: 484px;
    height: 291px;
    background: var(--card);
    border-radius: 12px;
    overflow: hidden;
  }
  .card--front { left: 102px; }
  .card--back { left: 596px; width: 480px; }

  /* Front */
  .front-brand {
    position: absolute;
    left: 0; right: 0; top: 104px;
    text-align: center;
    color: var(--brown-dark);
    font-weight: 700;
  }
  .front-brand .brand-name {
    display: block;
    font-size: 54px;
    line-height: 1;
    letter-spacing: 1px;
    text-transform: uppercase;
  }
  .front-brand .brand-suffix {
    display: block;
    font-size: 15px;
    letter-spacing: 2px;
    margin-top: 6px;
    text-transform: uppercase;
  }
  .brand-square {
    display: block;
    width: 26px; height: 26px;
    margin: 0 auto 14px;
    background: var(--tan);
  }
  .front-band {
    position: absolute;
    left: 0; right: 0; bottom: 0;
    height: 29px;
    background: linear-gradient(90deg, var(--tan) 0%, var(--brown-mid) 100%);
    color: var(--white);
    font-size: 13px;
    line-height: 29px;
    text-align: center;
  }

  /* Back */
  .contact {
    position: absolute;
    left: 28px; top: 40px;
    color: var(--ink-soft);
  }
  .contact-label {
    display: flex;
    align-items: center;
    gap: 4px;
    font-size: 8.5px;
    width: 174px;
  }
  .contact-label::after {
    content: "";
    flex: 1;
    height: 1px;
    background: #9b8f85;
  }
  .contact-name {
    margin-top: 9px;
    font-size: 19px;
    font-weight: 700;
    color: var(--brown-dark);
    text-transform: uppercase;
    letter-spacing: 0.3px;
  }
  .contact-name .surname { color: var(--tan); }
  .contact-line {
    display: flex;
    align-items: flex-start;
    gap: 6px;
    margin-top: 5px;
    font-size: 12px;
    line-height: 16px;
  }
  .contact-line svg { flex: none; margin-top: 3px; }
  .back-motto {
    position: absolute;
    left: 28px; top: 163px;
    font-size: 11.5px;
    line-height: 15px;
    color: var(--ink-soft);
  }
  .back-brand {
    position: absolute;
    left: 270px; width: 200px; top: 44px;
    text-align: center;
    color: var(--brown-dark);
    font-weight: 700;
  }
  .back-brand .brand-square { width: 28px; height: 28px; margin-bottom: 16px; }
  .back-brand .brand-name {
    display: block;
    font-size: 38px;
    line-height: 1;
    text-transform: uppercase;
    letter-spacing: 0.5px;
  }
  .back-brand .brand-suffix {
    display: block;
    font-size: 11.5px;
    letter-spacing: 1.5px;
    margin-top: 4px;
    text-transform: uppercase;
  }
  .wave {
    position: absolute;
    left: 0; top: 0;
    width: 480px; height: 291px;
  }
  .pitch {
    position: absolute;
    right: 27px; top: 197px;
    text-align: right;
    color: var(--white);
    font-size: 13px;
    line-height: 18.5px;
  }
</style>
</head>
<body>

  <section class="card card--front" aria-label="Business card front">
    <div class="front-brand">
      <span class="brand-square" aria-hidden="true"></span>
      <span class="brand-name">Tolbek</span>
      <span class="brand-suffix">Builders LLC</span>
    </div>
    <div class="front-band">Committed to Quality, Service &amp; Integrity</div>
  </section>

  <section class="card card--back" aria-label="Business card back">
    <svg class="wave" viewBox="0 0 480 291" aria-hidden="true">
      <defs>
        <linearGradient id="swoosh" x1="0" x2="1" y1="0" y2="0">
          <stop offset="0" stop-color="#c2a98d"/>
          <stop offset="1" stop-color="#8a6b52"/>
        </linearGradient>
      </defs>
      <path d="M0 222 C 70 250, 150 262, 230 240 C 320 212, 380 168, 480 160 L480 170 C 390 176, 330 220, 240 250 C 160 274, 70 262, 0 236 Z" fill="url(#swoosh)"/>
      <path d="M40 238 C 110 258, 190 262, 270 240 C 200 268, 110 266, 40 238 Z" fill="#8a6b52"/>
      <path d="M0 272 C 90 300, 190 280, 280 232 C 360 190, 420 180, 480 180 L480 291 L0 291 Z" fill="var(--brown-dark)"/>
    </svg>

    <div class="contact">
      <div class="contact-label">Contact:</div>
      <div class="contact-name">Dale <span class="surname">Whitacre</span></div>
      <div class="contact-line">
        <svg width="10" height="10" viewBox="0 0 10 10" aria-hidden="true">
          <circle cx="5" cy="5" r="4.4" fill="none" stroke="#8a7564" stroke-width="0.9"/>
          <path d="M3.3 2.6 L4.2 3.6 L3.7 4.2 C4.1 5 4.8 5.7 5.6 6.1 L6.2 5.6 L7.2 6.5 L6.6 7.3 C4.9 7.2 2.8 5.1 2.6 3.3 Z" fill="#8a7564"/>
        </svg>
        <span>610-555-0187</span>
      </div>
      <div class="contact-line">
        <svg width="10" height="12" viewBox="0 0 10 12" aria-hidden="true">
          <path d="M5 11.4 C2.4 8 1 6.2 1 4.4 A4 4 0 0 1 9 4.4 C9 6.2 7.6 8 5 11.4 Z" fill="none" stroke="#8a7564" stroke-width="1"/>
          <circle cx="5" cy="4.4" r="1.4" fill="#8a7564"/>
        </svg>
        <span>4076 Copper Ridge RD,<br>Millbrook, PA 16790</span>
      </div>
    </div>

    <p class="back-motto">Committed to Quality,<br>Service &amp; Integrity</p>

    <div class="back-brand">
      <span class="brand-square" aria-hidden="true"></span>
      <span class="brand-name">Tolbek</span>
      <span class="brand-suffix">Builders LLC</span>
    </div>

    <p class="pitch">Are you<br>thinking about a new<br>building on your property,<br>or renovating an existing structure?</p>
  </section>

</body>
</html>
```